Presentation Of Our Epidemiology Consulting Framework

We need a slide deck (png files) for PowerPoint that describes our organization and type of clients we serve, and our 6 phase framework that explains how we work with clients. Please use the minimum amount of text on each slide.  We want a more visual display of how to work with us. We want it to look very similar to our brochure.  We want to also have a few extra branded slides without text that can be used as a template if we decide to add to the deck later or create a new slide deck.
Colors
#56588C
#F28444
#F2E088
#F24C27
#ODODOD

```html
<!DOCTYPE html>
<html lang="en">
<head>
<meta charset="utf-8">
<title>DrAMVance Framework – Slide Deck</title>
<link href="https://fonts.googleapis.com/css2?family=Bebas+Neue&family=Oswald:wght@500;600&family=Dancing+Script:wght@700&family=Montserrat:wght@400;500;600;700&family=Roboto:wght@400&display=swap" rel="stylesheet">
<style>
  :root {
    --navy-deep: #17163a;
    --navy: #24225a;
    --indigo: #56588C;
    --indigo-bright: #4d4a9e;
    --orange: #F28444;
    --orange-hot: #F24C27;
    --orange-mid: #ee6a2b;
    --ink: #0D0D0D;
    --white: #ffffff;
    --paper: #ffffff;
    --head: "Bebas Neue", "Oswald", sans-serif;
    --head-mixed: "Oswald", "Arial Narrow", sans-serif;
    --body: "Montserrat", "Helvetica Neue", Arial, sans-serif;
    --label: "Roboto", Arial, sans-serif;
    --script: "Dancing Script", cursive;
  }
  * { box-sizing: border-box; margin: 0; padding: 0; }
  html, body { width: 990px; height: 1200px; overflow: hidden; background: var(--paper); }
  .canvas { position: relative; width: 990px; height: 1200px; font-family: var(--body); color: var(--ink); }

  .slide { position: absolute; width: 432px; height: 243px; overflow: hidden; background: var(--white);
           box-shadow: 0 2px 6px rgba(0,0,0,.18); }
  .slide-bg { position: absolute; inset: 0; width: 432px; height: 243px; }
  .abs { position: absolute; }

  .brand { position: absolute; display: flex; align-items: center; gap: 4px;
           font-family: var(--body); font-weight: 700; font-size: 12px; color: var(--indigo); letter-spacing: -.2px; white-space: nowrap; }
  .brand-dot { width: 11px; height: 11px; border-radius: 50%; background: var(--orange-mid); }

  .phase-label { position: absolute; left: 20px; top: 17px; font-family: var(--body); font-weight: 600;
                 font-size: 12.5px; color: var(--white); }
  .phase-label::after { content: ""; position: absolute; left: 0; top: 18px; width: 31px; height: 2px; background: var(--orange-mid); }
  .phase-title { position: absolute; left: 21px; font-family: var(--head); font-size: 26px; line-height: 27px;
                 color: var(--white); letter-spacing: .4px; white-space: nowrap; }
  .section-head { position: absolute; font-family: var(--head); font-size: 13px; color: var(--ink); letter-spacing: .3px; white-space: nowrap; }
  .body-copy { font-family: var(--body); font-size: 7px; line-height: 11px; color: #222; }

  /* title slide */
  .script-kicker { left: 20px; top: 16px; font-family: var(--script); font-size: 15px; color: var(--orange); }
  .hero-title { left: 20px; top: 44px; font-family: var(--head-mixed); font-weight: 600; font-size: 19px; line-height: 22px; color: var(--white); white-space: nowrap; }
  .hero-pill { left: 21px; top: 94px; width: 114px; height: 20px; border-radius: 10px; background: var(--orange-hot);
               color: var(--white); font-weight: 600; font-size: 9px; display: flex; align-items: center; justify-content: center; }
  .hero-framework { left: 20px; top: 118px; font-family: var(--head); font-size: 28px; color: var(--indigo-bright); letter-spacing: .5px; }
  .hero-cta { left: 195px; top: 224px; font-size: 7px; font-weight: 600; color: var(--ink); white-space: nowrap; }

  /* phase 1 */
  .step-row { position: absolute; left: 218px; display: flex; align-items: center; gap: 14px; }
  .step-diamond { flex: none; width: 24px; height: 24px; transform: rotate(45deg); border-radius: 3px;
                  background: linear-gradient(135deg, var(--indigo-bright), var(--navy)); box-shadow: 1px 1px 2px rgba(0,0,0,.3);
                  margin-left: 6px; margin-right: 4px; display: flex; align-items: center; justify-content: center; }
  .step-diamond span { width: 9px; height: 9px; border: 1.2px solid var(--white); border-radius: 2px; transform: rotate(-45deg); }
  .step-text { width: 150px; }

  /* phase 2 */
  .hub { position: absolute; left: 270px; top: 97px; width: 78px; height: 78px; border-radius: 50%;
         background: var(--indigo-bright); display: flex; align-items: center; justify-content: center;
         color: var(--white); font-weight: 700; font-size: 9px; }
  .hub-label { position: absolute; font-family: var(--label); font-size: 7px; line-height: 12px; color: #222; white-space: nowrap; }
  .hub-label.to-left { text-align: right; }

  /* phase 3 */
  .task { position: absolute; display: flex; align-items: center; gap: 8px; }
  .task-icon { flex: none; width: 31px; height: 28px; border-radius: 2px; display: flex; align-items: center; justify-content: center; }
  .task-icon.dark { background: linear-gradient(160deg, var(--indigo-bright), var(--navy-deep)); }
  .task-icon.warm { background: var(--orange-mid); }
  .task-icon svg { width: 16px; height: 16px; }
  .task p { font-family: var(--label); font-size: 7.3px; line-height: 11px; white-space: nowrap; }

  /* phase 4 */
  .step-pill { position: absolute; left: 216px; width: 195px; height: 25px; border-radius: 13px;
               display: flex; align-items: center; gap: 7px; padding-left: 4px; color: var(--white); font-weight: 700; font-size: 6.4px; }
  .step-pill.cool { background: var(--navy); }
  .step-pill.warm { background: var(--orange-mid); }
  .pill-badge { width: 17px; height: 17px; border-radius: 50%; background: var(--white); display: flex; align-items: center; justify-content: center; }
  .pill-badge span { width: 7px; height: 7px; border-radius: 50%; border: 1.3px solid var(--indigo); }
  .step-pill.warm .pill-badge span { border-color: var(--orange-mid); }

  /* phase 5 */
  .deliver-diamond { position: absolute; left: 293px; width: 30px; height: 30px; transform: rotate(45deg); }
  .deliver-diamond.cool { background: linear-gradient(135deg, var(--indigo-bright), var(--navy-deep)); }
  .deliver-diamond.warm { background: linear-gradient(135deg, var(--orange), var(--orange-hot)); }
  .deliver-label { position: absolute; font-size: 8.3px; line-height: 12.5px; color: #222; white-space: nowrap; }
  .deliver-label.to-left { text-align: right; }

  /* closing slide */
  .close-head { left: 268px; top: 20px; width: 150px; font-family: var(--head-mixed); font-weight: 500; font-size: 12px; line-height: 16px; color: var(--white); }
  .close-copy { left: 268px; top: 62px; width: 140px; font-size: 7.4px; line-height: 11px; color: var(--white); }
  .contact { position: absolute; left: 268px; display: flex; align-items: center; gap: 9px; color: var(--white); font-size: 8.6px; font-weight: 500; white-space: nowrap; }
  .contact svg { width: 12px; height: 12px; }
  .social { position: absolute; top: 218px; width: 15px; height: 15px; border-radius: 50%; border: 1px solid var(--indigo); }
</style>
</head>
<body>
<main class="canvas">

  <!-- Title slide -->
  <section class="slide slide-title" style="left:46px;top:50px;">
    <svg class="slide-bg" viewBox="0 0 432 243" aria-hidden="true">
      <defs>
        <linearGradient id="darkA" x1="0" y1="0" x2="1" y2="1"><stop offset="0" stop-color="#1a1842"/><stop offset="1" stop-color="#2b2870"/></linearGradient>
      </defs>
      <rect width="432" height="243" fill="url(#darkA)"/>
      <circle cx="333" cy="62" r="130" fill="#ee6a2b"/>
      <circle cx="333" cy="62" r="122" fill="#ffffff"/>
      <path d="M0,190 C70,165 150,168 240,198 C320,224 390,212 432,172 L432,243 L0,243 Z" fill="#ffffff"/>
      <path d="M220,200 C300,230 380,225 432,180 L432,188 C385,232 300,238 220,204 Z" fill="#ee6a2b"/>
      <rect x="0" y="241" width="432" height="2" fill="#ee6a2b"/>
    </svg>
    <svg class="abs" style="left:219px;top:-52px;" width="228" height="228" viewBox="0 0 228 228" role="img" aria-label="Portrait photograph of the consultant">
      <defs><radialGradient id="heroPhoto" cx=".5" cy=".45" r=".6"><stop offset="0" stop-color="#5a4fb0"/><stop offset="1" stop-color="#2a2568"/></radialGradient></defs>
      <circle cx="114" cy="114" r="114" fill="url(#heroPhoto)"/>
    </svg>
    <div class="abs script-kicker">Transforming</div>
    <div class="abs hero-title">Health Data into<br>Community Impact</div>
    <div class="abs hero-pill">The DrAMVance</div>
    <div class="abs hero-framework">FRAMEWORK</div>
    <div class="brand" style="left:24px;top:204px;font-size:15px;"><span class="brand-dot"></span>DrAMVance</div>
    <div class="abs hero-cta">READY TO TRANSFORM YOUR HEALTH COMMUNICATION?</div>
  </section>

  <!-- Phase 1 -->
  <section class="slide slide-phase" style="left:512px;top:50px;">
    <svg class="slide-bg" viewBox="0 0 432 243" aria-hidden="true">
      <defs><linearGradient id="darkB" x1="0" y1="0" x2="0" y2="1"><stop offset="0" stop-color="#1c1a46"/><stop offset="1" stop-color="#15143a"/></linearGradient></defs>
      <rect width="432" height="243" fill="url(#darkB)"/>
      <path d="M164,0 C140,45 145,88 170,135 C193,180 185,220 160,243 L432,243 L432,0 Z" fill="#ee6a2b"/>
      <path d="M170,0 C146,45 151,88 176,135 C199,180 193,220 168,243 L432,243 L432,0 Z" fill="#ffffff"/>
    </svg>
    <div class="phase-label">PHASE 1</div>
    <div class="phase-title" style="top:84px;">DISCOVERY<br>&amp; VISION<br>ALIGNMENT</div>
    <div class="brand" style="left:300px;top:10px;"><span class="brand-dot"></span>DrAMVance</div>
    <div class="section-head" style="left:217px;top:36px;">BUILDING THE FOUNDATION FOR SUCCESS</div>
    <div class="step-row" style="top:62px;"><div class="step-diamond"><span></span></div><p class="body-copy step-text">Deep-dive exploration of your organization's unique challenges and opportunities</p></div>
    <div class="step-row" style="top:108px;"><div class="step-diamond"><span></span></div><p class="body-copy step-text">Strategic alignment of goals and expectations</p></div>
    <div class="step-row" style="top:154px;"><div class="step-diamond"><span></span></div><p class="body-copy step-text">Custom-tailored solution design</p></div>
    <div class="step-row" style="top:196px;"><div class="step-diamond"><span></span></div><p class="body-copy step-text">Clear roadmap development with defined milestones</p></div>
  </section>

  <!-- Phase 2 -->
  <section class="slide slide-phase" style="left:46px;top:335px;">
    <svg class="slide-bg" viewBox="0 0 432 243" aria-hidden="true">
      <defs><linearGradient id="darkC" x1="0" y1="0" x2="0" y2="1"><stop offset="0" stop-color="#1c1a46"/><stop offset="1" stop-color="#15143a"/></linearGradient></defs>
      <rect width="432" height="243" fill="url(#darkC)"/>
      <path d="M164,0 C140,45 145,88 170,135 C193,180 185,220 160,243 L432,243 L432,0 Z" fill="#ee6a2b"/>
      <path d="M170,0 C146,45 151,88 176,135 C199,180 193,220 168,243 L432,243 L432,0 Z" fill="#ffffff"/>
      <g stroke="#333" stroke-width=".5" fill="#ee6a2b">
        <line x1="260" y1="99" x2="280" y2="99"/><circle cx="260" cy="99" r="1.3" stroke="none"/>
        <line x1="338" y1="98" x2="357" y2="98"/><circle cx="357" cy="98" r="1.3" fill="#24225a" stroke="none"/>
        <line x1="261" y1="148" x2="272" y2="148"/><circle cx="261" cy="148" r="1.3" stroke="none"/>
        <line x1="346" y1="147" x2="358" y2="147"/><circle cx="358" cy="147" r="1.3" fill="#24225a" stroke="none"/>
        <line x1="309" y1="175" x2="309" y2="190"/><circle cx="309" cy="190" r="1.3" fill="#24225a" stroke="none"/>
      </g>
    </svg>
    <div class="phase-label">PHASE 2</div>
    <div class="phase-title" style="top:86px;">PARTNERSHIP<br>LAUNCH</div>
    <div class="brand" style="left:300px;top:10px;"><span class="brand-dot"></span>DrAMVance</div>
    <div class="section-head" style="left:232px;top:60px;">SETTING THE STAGE FOR EXCELLENCE</div>
    <div class="hub">DrAMVance</div>
    <p class="hub-label to-left" style="right:175px;top:92px;">Formation of dedicated<br>project team</p>
    <p class="hub-label" style="left:360px;top:91px;">Comprehensive<br>data gathering</p>
    <p class="hub-label to-left" style="right:174px;top:142px;">Establishment of<br>collaborative workflow</p>
    <p class="hub-label" style="left:361px;top:141px;">Strategic timeline<br>planning</p>
    <p class="hub-label" style="left:250px;top:192px;width:120px;text-align:center;">Stakeholder engagement and<br>vision capture</p>
  </section>

  <!-- Phase 3 -->
  <section class="slide slide-phase" style="left:512px;top:335px;">
    <svg class="slide-bg" viewBox="0 0 432 243" aria-hidden="true">
      <defs><linearGradient id="darkD" x1="0" y1="0" x2="0" y2="1"><stop offset="0" stop-color="#1c1a46"/><stop offset="1" stop-color="#15143a"/></linearGradient></defs>
      <rect width="432" height="243" fill="url(#darkD)"/>
      <path d="M164,0 C140,45 145,88 170,135 C193,180 185,220 160,243 L432,243 L432,0 Z" fill="#ee6a2b"/>
      <path d="M170,0 C146,45 151,88 176,135 C199,180 193,220 168,243 L432,243 L432,0 Z" fill="#ffffff"/>
    </svg>
    <div class="phase-label">PHASE 3</div>
    <div class="phase-title" style="top:86px;">EXPERT<br>EXECUTION</div>
    <div class="brand" style="left:300px;top:10px;"><span class="brand-dot"></span>DrAMVance</div>
    <div class="section-head" style="left:215px;top:35px;">WHERE SCIENCE MEETS SERVICE</div>
    <p class="abs body-copy" style="left:216px;top:57px;font-size:7.8px;line-height:13px;">Our specialized team begins the<br>transformation process:</p>
    <div class="task" style="left:216px;top:95px;">
      <div class="task-icon dark"><svg viewBox="0 0 16 16" fill="none" stroke="#fff" stroke-width="1.2"><path d="M2 14V9M6 14V6M10 14V8M14 14V3"/></svg></div>
      <p>In-depth research<br>and analysis</p>
    </div>
    <div class="task" style="right:21px;top:126px;">
      <p style="text-align:right;">Content development and<br>refinement</p>
      <div class="task-icon warm"><svg viewBox="0 0 16 16" fill="none" stroke="#fff" stroke-width="1.2"><rect x="2" y="3" width="12" height="8"/><path d="M6 14h4M8 11v3"/></svg></div>
    </div>
    <div class="task" style="left:216px;top:161px;">
      <div class="task-icon dark"><svg viewBox="0 0 16 16" fill="none" stroke="#fff" stroke-width="1.2"><rect x="2" y="2" width="12" height="12"/><path d="M4 11l3-3 2 2 4-4"/></svg></div>
      <p>Data interpretation<br>and visualization</p>
    </div>
    <div class="task" style="right:21px;top:194px;">
      <p style="text-align:right;">Plain language translation of<br>complex health information</p>
      <div class="task-icon warm"><svg viewBox="0 0 16 16" fill="none" stroke="#fff" stroke-width="1.2"><circle cx="8" cy="7" r="4.5"/><path d="M6 14h4"/></svg></div>
    </div>
  </section>

  <!-- Blank branded template -->
  <section class="slide slide-blank" style="left:46px;top:620px;">
    <svg class="slide-bg" viewBox="0 0 432 243" aria-hidden="true">
      <defs><linearGradient id="blankGrad" x1="0" y1="1" x2="1" y2="0"><stop offset="0" stop-color="#16153a"/><stop offset="1" stop-color="#4e4a9c"/></linearGradient></defs>
      <rect width="432" height="243" fill="url(#blankGrad)"/>
      <rect x="12" y="10" width="408" height="223" fill="none" stroke="#ffffff" stroke-width=".8"/>
    </svg>
  </section>

  <!-- Phase 4 -->
  <section class="slide slide-phase" style="left:512px;top:620px;">
    <svg class="slide-bg" viewBox="0 0 432 243" aria-hidden="true">
      <defs><linearGradient id="darkE" x1="0" y1="0" x2="0" y2="1"><stop offset="0" stop-color="#1c1a46"/><stop offset="1" stop-color="#15143a"/></linearGradient></defs>
      <rect width="432" height="243" fill="url(#darkE)"/>
      <path d="M164,0 C140,45 145,88 170,135 C193,180 185,220 160,243 L432,243 L432,0 Z" fill="#ee6a2b"/>
      <path d="M170,0 C146,45 151,88 176,135 C199,180 193,220 168,243 L432,243 L432,0 Z" fill="#ffffff"/>
    </svg>
    <div class="phase-label">PHASE 4</div>
    <div class="phase-title" style="top:86px;">COLLABORATIVE<br>REFINEMENT</div>
    <div class="brand" style="left:300px;top:10px;"><span class="brand-dot"></span>DrAMVance</div>
    <div class="section-head" style="left:215px;top:44px;">WHERE SCIENCE MEETS SERVICE</div>
    <p class="abs body-copy" style="left:216px;top:66px;font-size:7.8px;">Ensuring Perfect Alignment</p>
    <div class="step-pill cool" style="top:87px;"><span class="pill-badge"><span></span></span>Presentation of initial frameworks</div>
    <div class="step-pill warm" style="top:118px;"><span class="pill-badge"><span></span></span>Interactive feedback sessions</div>
    <div class="step-pill cool" style="top:150px;"><span class="pill-badge"><span></span></span>Draft review and optimization</div>
    <div class="step-pill warm" style="top:181px;"><span class="pill-badge"><span></span></span>Stakeholder input integration</div>
  </section>

  <!-- Phase 5 -->
  <section class="slide slide-phase" style="left:44px;top:902px;">
    <svg class="slide-bg" viewBox="0 0 432 243" aria-hidden="true">
      <defs><linearGradient id="darkF" x1="0" y1="0" x2="0" y2="1"><stop offset="0" stop-color="#1c1a46"/><stop offset="1" stop-color="#15143a"/></linearGradient></defs>
      <rect width="432" height="243" fill="url(#darkF)"/>
      <path d="M164,0 C140,45 145,88 170,135 C193,180 185,220 160,243 L432,243 L432,0 Z" fill="#ee6a2b"/>
      <path d="M170,0 C146,45 151,88 176,135 C199,180 193,220 168,243 L432,243 L432,0 Z" fill="#ffffff"/>
    </svg>
    <div class="phase-label">PHASE 5</div>
    <div class="phase-title" style="top:84px;">IMPACT<br>DELIVERY</div>
    <div class="brand" style="left:300px;top:10px;"><span class="brand-dot"></span>DrAMVance</div>
    <div class="section-head" style="left:240px;top:44px;">BRINGING VISION TO REALITY</div>
    <div class="deliver-diamond cool" style="top:75px;"></div>
    <div class="deliver-diamond warm" style="top:112px;"></div>
    <div class="deliver-diamond cool" style="top:147px;"></div>
    <div class="deliver-diamond warm" style="top:184px;"></div>
    <p class="deliver-label to-left" style="right:151px;top:77px;">Final deliverable<br>presentation</p>
    <p class="deliver-label" style="left:335px;top:118px;">Implementation<br>support</p>
    <p class="deliver-label to-left" style="right:151px;top:145px;">Knowledge<br>transfer</p>
    <p class="deliver-label" style="left:335px;top:183px;">Impact<br>measurement<br>framework</p>
  </section>

  <!-- Closing slide -->
  <section class="slide slide-close" style="left:512px;top:902px;">
    <svg class="slide-bg" viewBox="0 0 432 243" aria-hidden="true">
      <defs><linearGradient id="darkG" x1="0" y1="0" x2="1" y2="1"><stop offset="0" stop-color="#1c1a46"/><stop offset="1" stop-color="#16153a"/></linearGradient></defs>
      <rect width="432" height="243" fill="url(#darkG)"/>
      <path d="M0,0 L252,0 C268,70 255,150 210,182 C160,212 70,208 0,178 Z" fill="#ee6a2b"/>
      <path d="M0,205 C110,222 210,196 300,180 C360,170 405,172 432,176 L432,243 L0,243 Z" fill="#ffffff"/>
      <path d="M0,196 C110,214 210,190 300,174 C360,164 405,166 432,170 L432,176 C405,172 360,170 300,180 C210,196 110,222 0,205 Z" fill="#2b2870"/>
      <rect x="0" y="241" width="432" height="2" fill="#ee6a2b"/>
    </svg>
    <svg class="abs" style="left:0;top:0;" width="250" height="200" viewBox="0 0 250 200" role="img" aria-label="Photograph of a doctor working at a laptop in a clinic">
      <defs><linearGradient id="closePhoto" x1="0" y1="0" x2="1" y2="1"><stop offset="0" stop-color="#e9e4de"/><stop offset="1" stop-color="#b9b3ad"/></linearGradient></defs>
      <path d="M0,0 L240,0 C255,70 243,145 202,174 C155,203 68,198 0,170 Z" fill="url(#closePhoto)"/>
    </svg>
    <div class="abs close-head">Ready to Transform Your Health Communication?</div>
    <p class="abs close-copy">Contact us to begin your journey toward more effective, equitable health communication.</p>
    <div class="contact" style="top:104px;">
      <svg viewBox="0 0 12 12" fill="none" stroke="#fff" stroke-width="1.1"><path d="M2.5 1.5l2 2-1 1.3c.7 1.4 1.8 2.5 3.2 3.2l1.3-1 2 2-1.2 1.5C5.3 10.2 1.8 6.7 1 3z"/></svg>
      +1 555 014 2290
    </div>
    <div class="contact" style="top:129px;">
      <svg viewBox="0 0 12 12" fill="none" stroke="#fff" stroke-width="1.1"><rect x="1" y="2.5" width="10" height="7"/><path d="M1 2.5l5 4 5-4"/></svg>
      hello@dramvance.com
    </div>
    <div class="brand" style="left:280px;top:203px;font-size:15px;"><span class="brand-dot"></span>DrAMVance</div>
    <span class="social" style="left:39px;"></span>
    <span class="social" style="left:59px;"></span>
  </section>

</main>
</body>
</html>
```